Flyer for Leaflet Dropping - A5 - Managed IT Support Flyer

I need an A5 double sided flyer LANDSCAPE - design for door to door leaflet dropping / marketing to local businesses.
Our main aim is to promote our ‘Managed IT Support’ services to local small and medium businesses.
Our secondary aim is to promote our additional services which are internet/communications and cloud services. We want to mention these services but they are only secondary therefore need to take a smaller focus and not detract from the main message of the flyer.
• Hosted Cloud Desktop
• VOIP Telephone Systems
• Desk Suite
• Cloud Services
• Internet Services
• Disaster Recovery

Target Market(s)

Our target audience is senior members of company (MD, FD, Owners, Operations, Management), looking to outsource their IT requirements/needs. UK Only. N London

Industry/Entity Type

Information Technology

Font styles to use
Sans Serif

Requirements
Must have
• Please use the website for a source of information and inspiration – www.brantowork.co.uk.
• We specifically feel the points below are important and want to see them feature.
• 1. Large bold heading highlighting our primary service ‘Managed IT Support’
• 2. Secondary sub-heading explaining exactly what we do.
• ‘We manage your IT ensuring systems are monitored, supported and protected to enhance business growth.’
• 3. Reasons to choose BrantoWork – take inspiration from https://www.brantowork.co.uk/about-us/
• 4. No Risk - Our 90 Day Satisfaction Guarantee (see website).
• 5. Areas we cover: ‘Trusted by 100+ businesses across Hertfordshire, Essex, London & beyond.‘
• 6. Name of company, contact details.
• CALL TO ACTION
• 1. Call Us – 03337215946
• 2. Visit our Website – https://www.brantowork.co.uk/gomanaged

```html
<!DOCTYPE html>
<html lang="en">
<head>
<meta charset="utf-8">
<title>BrantoWork – Managed IT Support A5 Flyer</title>
<link rel="stylesheet" href="https://fonts.googleapis.com/css2?family=Open+Sans:wght@400;600;700;800&display=swap">
<style>
  :root {
    --orange: #f28a1c;
    --orange-deep: #e5700f;
    --blue: #1f63b4;
    --blue-light: #2c9ad8;
    --blue-deep: #174a93;
    --white: #ffffff;
    --ink: #5a5a5a;
    --ink-soft: #9a9a9a;
    --stage: #e4e4e4;
  }
  * { box-sizing: border-box; margin: 0; padding: 0; }
  html, body { width: 1200px; height: 961px; overflow: hidden; }
  body {
    background: var(--stage);
    font-family: "Open Sans", Arial, sans-serif;
    position: relative;
  }
  .flyer {
    position: absolute;
    left: 280px;
    width: 640px;
    height: 452px;
    background: var(--white);
    overflow: hidden;
    box-shadow: 0 6px 18px rgba(0,0,0,.18);
  }
  .flyer--front { top: 16px; }
  .flyer--back { top: 492px; }
  .flyer__shapes { position: absolute; inset: 0; }
  .abs { position: absolute; }

  /* header band */
  .band {
    position: absolute; left: 0; top: 0; width: 100%;
    background: linear-gradient(90deg, var(--orange-deep), var(--orange));
    color: var(--white);
  }
  .band--front { height: 70px; text-align: center; }
  .band__title {
    font-weight: 700; font-size: 25px; letter-spacing: .3px;
    margin-top: 8px; display: inline-flex; align-items: center; gap: 14px;
  }
  .band__title::before, .band__title::after {
    content: ""; width: 50px; height: 1px; background: rgba(255,255,255,.8);
  }
  .band__sub { font-size: 12.5px; margin-top: 4px; }
  .band--back { height: 46px; padding: 14px 0 0 22px; }
  .band--back .band__title { font-size: 14px; margin: 0; }
  .band--back .band__title::before, .band--back .band__title::after { display: none; }

  /* brand */
  .brand { position: absolute; left: 22px; }
  .brand__row { display: flex; align-items: center; gap: 8px; }
  .brand__dot { width: 14px; height: 14px; border-radius: 50%; background: var(--orange); }
  .brand__name { font-size: 27px; font-weight: 400; color: var(--ink); letter-spacing: -.3px; }
  .brand__tag { font-size: 9px; color: var(--ink-soft); margin: 3px 0 0 22px; }

  /* reasons */
  .reasons__title { left: 190px; top: 252px; color: var(--white); font-weight: 700; font-size: 13.5px; white-space: nowrap; }
  .reasons { list-style: none; color: var(--white); font-size: 8.6px; }
  .reasons li { display: flex; align-items: center; gap: 6px; height: 18px; white-space: nowrap; }
  .reasons--a { left: 190px; top: 278px; }
  .reasons--b { left: 365px; top: 280px; }
  .tick { width: 12px; height: 12px; flex: none; }
  .intro {
    left: 190px; top: 374px; width: 430px;
    color: var(--white); font-size: 8.6px; line-height: 1.3;
  }

  /* footer bar */
  .footer {
    position: absolute; left: 0; bottom: 0; width: 100%; height: 42px;
    background: linear-gradient(90deg, var(--orange), var(--orange-deep));
    color: var(--white);
    display: flex; align-items: center; justify-content: space-between;
    padding: 0 20px;
  }
  .contact { display: flex; align-items: center; gap: 7px; font-size: 12px; font-weight: 600; white-space: nowrap; }
  .contact--phone { font-size: 19px; font-weight: 700; letter-spacing: .5px; }
  .contact svg { flex: none; }

  /* back content */
  .guarantee { left: 22px; top: 262px; width: 320px; color: var(--white); }
  .guarantee__title { font-size: 12.5px; font-weight: 700; margin-bottom: 6px; }
  .guarantee__text { font-size: 9px; line-height: 1.4; }
  .services { left: 362px; top: 226px; color: var(--white); }
  .services__title { font-size: 9.5px; font-weight: 600; margin-bottom: 8px; letter-spacing: .1px; white-space: nowrap; }
  .services__list { list-style: none; font-size: 9.5px; }
  .services__list li { display: flex; align-items: center; gap: 6px; height: 17px; }
</style>
</head>
<body>

<!-- Front side -->
<section class="flyer flyer--front" aria-label="Flyer front">
  <svg class="flyer__shapes" viewBox="0 0 640 452" aria-hidden="true">
    <defs>
      <linearGradient id="blueFront" x1="0" y1="0" x2="1" y2="0">
        <stop offset="0" stop-color="#2c9ad8"/>
        <stop offset="0.55" stop-color="#1f63b4"/>
        <stop offset="1" stop-color="#174a93"/>
      </linearGradient>
    </defs>
    <path d="M0,200 C200,180 480,230 640,330 L640,410 L0,410 Z" fill="url(#blueFront)"/>
    <path d="M0,188 C200,168 480,218 640,318 L640,330 C480,230 200,180 0,200 Z" fill="#d6d9dd"/>
  </svg>
  <div class="abs" role="img" aria-label="Photo of staff working at desks in a bright open-plan office"
       style="left:0;top:0;width:640px;height:452px;background:linear-gradient(135deg,#dfe2e5,#7e868f);clip-path:path('M215,70 L640,70 L640,318 C480,218 300,176 170,182 C200,150 210,110 215,70 Z');"></div>
  <div class="abs" role="img" aria-label="Photo of two smartphones showing a VOIP dialler app"
       style="left:22px;top:196px;width:140px;height:188px;border-radius:12px;background:linear-gradient(160deg,#4a4f56,#15181c);"></div>

  <header class="band band--front">
    <h1 class="band__title">MANAGED IT SUPPORT</h1>
    <p class="band__sub">We manage your IT ensuring systems are monitored, supported and protected to enhance business growth.</p>
  </header>

  <div class="brand" style="top:92px;">
    <div class="brand__row"><span class="brand__dot"></span><span class="brand__name">BrantoWork</span></div>
    <p class="brand__tag">Helping you work smarter</p>
  </div>

  <h2 class="abs reasons__title">10 REASONS TO CHOOSE BRANTOWORK</h2>
  <ul class="abs reasons reasons--a">
    <li><svg class="tick" viewBox="0 0 12 12"><circle cx="6" cy="6" r="5.3" fill="none" stroke="#fff"/><path d="M3.5,6.2 5.2,7.8 8.5,4.3" fill="none" stroke="#fff"/></svg>Super Fast Service</li>
    <li><svg class="tick" viewBox="0 0 12 12"><circle cx="6" cy="6" r="5.3" fill="none" stroke="#fff"/><path d="M3.5,6.2 5.2,7.8 8.5,4.3" fill="none" stroke="#fff"/></svg>Fully Accredited Partner</li>
    <li><svg class="tick" viewBox="0 0 12 12"><circle cx="6" cy="6" r="5.3" fill="none" stroke="#fff"/><path d="M3.5,6.2 5.2,7.8 8.5,4.3" fill="none" stroke="#fff"/></svg>Certified Technical Teams</li>
    <li><svg class="tick" viewBox="0 0 12 12"><circle cx="6" cy="6" r="5.3" fill="none" stroke="#fff"/><path d="M3.5,6.2 5.2,7.8 8.5,4.3" fill="none" stroke="#fff"/></svg>Industry Leading Client Portal</li>
    <li><svg class="tick" viewBox="0 0 12 12"><circle cx="6" cy="6" r="5.3" fill="none" stroke="#fff"/><path d="M3.5,6.2 5.2,7.8 8.5,4.3" fill="none" stroke="#fff"/></svg>Over 10 Years' Experience</li>
  </ul>
  <ul class="abs reasons reasons--b">
    <li><svg class="tick" viewBox="0 0 12 12"><circle cx="6" cy="6" r="5.3" fill="none" stroke="#fff"/><path d="M3.5,6.2 5.2,7.8 8.5,4.3" fill="none" stroke="#fff"/></svg>Dedicated Management Team</li>
    <li><svg class="tick" viewBox="0 0 12 12"><circle cx="6" cy="6" r="5.3" fill="none" stroke="#fff"/><path d="M3.5,6.2 5.2,7.8 8.5,4.3" fill="none" stroke="#fff"/></svg>Proactive Not Reactive Services</li>
    <li><svg class="tick" viewBox="0 0 12 12"><circle cx="6" cy="6" r="5.3" fill="none" stroke="#fff"/><path d="M3.5,6.2 5.2,7.8 8.5,4.3" fill="none" stroke="#fff"/></svg>Risk Free, 90 Day Money Back Guarantee</li>
    <li><svg class="tick" viewBox="0 0 12 12"><circle cx="6" cy="6" r="5.3" fill="none" stroke="#fff"/><path d="M3.5,6.2 5.2,7.8 8.5,4.3" fill="none" stroke="#fff"/></svg>A True, Full Service</li>
    <li><svg class="tick" viewBox="0 0 12 12"><circle cx="6" cy="6" r="5.3" fill="none" stroke="#fff"/><path d="M3.5,6.2 5.2,7.8 8.5,4.3" fill="none" stroke="#fff"/></svg>Big Enough To Deliver But Small Enough To Care</li>
  </ul>
  <p class="abs intro">We are an award winning IT support and strategic services company with over 10 years' experience of delivering exceptional service to small and medium sized organisations across all sectors.</p>

  <footer class="footer">
    <span class="contact"><svg width="14" height="11" viewBox="0 0 14 11"><rect x=".5" y=".5" width="13" height="10" rx="1.5" fill="none" stroke="#fff"/><path d="M1,1 7,6 13,1" fill="none" stroke="#fff"/></svg>support@brantowork.co.uk</span>
    <span class="contact contact--phone"><svg width="16" height="16" viewBox="0 0 16 16"><path d="M3,1 6,1 7,5 5,6.5 C6,8.8 7.2,10 9.5,11 L11,9 15,10 15,13 C15,14.2 14,15 13,15 C6.5,15 1,9.5 1,3 C1,2 2,1 3,1 Z" fill="#fff"/></svg>03337 215 946</span>
    <span class="contact"><svg width="13" height="13" viewBox="0 0 13 13"><circle cx="6.5" cy="6.5" r="5.8" fill="none" stroke="#fff"/><path d="M.7,6.5 H12.3 M6.5,.7 C3.5,4 3.5,9 6.5,12.3 M6.5,.7 C9.5,4 9.5,9 6.5,12.3" fill="none" stroke="#fff" stroke-width=".8"/></svg>www.brantowork.co.uk</span>
  </footer>
</section>

<!-- Back side -->
<section class="flyer flyer--back" aria-label="Flyer back">
  <svg class="flyer__shapes" viewBox="0 0 640 452" aria-hidden="true">
    <defs>
      <linearGradient id="blueBack" x1="0" y1="0" x2="1" y2="0">
        <stop offset="0" stop-color="#2c9ad8"/>
        <stop offset="0.5" stop-color="#1f63b4"/>
        <stop offset="1" stop-color="#174a93"/>
      </linearGradient>
    </defs>
    <path d="M0,232 C200,232 420,200 640,168 L640,410 L0,410 Z" fill="url(#blueBack)"/>
    <path d="M0,222 C200,222 420,190 640,158 L640,168 C420,200 200,232 0,232 Z" fill="#d6d9dd"/>
  </svg>
  <div class="abs" role="img" aria-label="Photo of a desktop monitor, laptop, tablet and phone showing office software"
       style="left:0;top:0;width:640px;height:452px;background:linear-gradient(135deg,#e8eaec,#9aa1a8);clip-path:path('M290,46 L640,46 L640,158 C420,190 280,212 230,214 C270,160 280,100 290,46 Z');"></div>

  <header class="band band--back">
    <h2 class="band__title">MANAGED IT SUPPORT SERVICES TO LOCAL BUSINESSES</h2>
  </header>

  <div class="brand" style="top:92px;">
    <div class="brand__row"><span class="brand__dot"></span><span class="brand__name">BrantoWork</span></div>
    <p class="brand__tag">Helping you work smarter</p>
  </div>

  <div class="abs guarantee">
    <h3 class="guarantee__title">NO RISK - Our 90 Day Satisfaction Guarantee</h3>
    <p class="guarantee__text">We are committed to providing you the best IT Support in the industry. If you do not see satisfactory results within 90 days, we will refund your money. How many IT support companies are willing to provide a guarantee for 90 days? To eliminate the stress and uncertainty of hiring a competent IT Support company, we've decided to offer our clients this ZERO RISK guarantee on all of our Managed Services.</p>
  </div>

  <div class="abs services">
    <h3 class="services__title">INTERNET/COMMUNICATIONS AND CLOUD SERVICES</h3>
    <ul class="services__list">
      <li><svg class="tick" viewBox="0 0 12 12"><circle cx="6" cy="6" r="5.3" fill="none" stroke="#fff"/><path d="M3.5,6.2 5.2,7.8 8.5,4.3" fill="none" stroke="#fff"/></svg>Hosted Cloud Desktop</li>
      <li><svg class="tick" viewBox="0 0 12 12"><circle cx="6" cy="6" r="5.3" fill="none" stroke="#fff"/><path d="M3.5,6.2 5.2,7.8 8.5,4.3" fill="none" stroke="#fff"/></svg>VOIP Telephone Systems</li>
      <li><svg class="tick" viewBox="0 0 12 12"><circle cx="6" cy="6" r="5.3" fill="none" stroke="#fff"/><path d="M3.5,6.2 5.2,7.8 8.5,4.3" fill="none" stroke="#fff"/></svg>Desk Suite</li>
      <li><svg class="tick" viewBox="0 0 12 12"><circle cx="6" cy="6" r="5.3" fill="none" stroke="#fff"/><path d="M3.5,6.2 5.2,7.8 8.5,4.3" fill="none" stroke="#fff"/></svg>Cloud Services</li>
      <li><svg class="tick" viewBox="0 0 12 12"><circle cx="6" cy="6" r="5.3" fill="none" stroke="#fff"/><path d="M3.5,6.2 5.2,7.8 8.5,4.3" fill="none" stroke="#fff"/></svg>Internet Services</li>
      <li><svg class="tick" viewBox="0 0 12 12"><circle cx="6" cy="6" r="5.3" fill="none" stroke="#fff"/><path d="M3.5,6.2 5.2,7.8 8.5,4.3" fill="none" stroke="#fff"/></svg>Disaster Recovery</li>
    </ul>
  </div>

  <footer class="footer">
    <span class="contact"><svg width="14" height="11" viewBox="0 0 14 11"><rect x=".5" y=".5" width="13" height="10" rx="1.5" fill="none" stroke="#fff"/><path d="M1,1 7,6 13,1" fill="none" stroke="#fff"/></svg>support@brantowork.co.uk</span>
    <span class="contact contact--phone"><svg width="16" height="16" viewBox="0 0 16 16"><path d="M3,1 6,1 7,5 5,6.5 C6,8.8 7.2,10 9.5,11 L11,9 15,10 15,13 C15,14.2 14,15 13,15 C6.5,15 1,9.5 1,3 C1,2 2,1 3,1 Z" fill="#fff"/></svg>03337 215 946</span>
    <span class="contact"><svg width="13" height="13" viewBox="0 0 13 13"><circle cx="6.5" cy="6.5" r="5.8" fill="none" stroke="#fff"/><path d="M.7,6.5 H12.3 M6.5,.7 C3.5,4 3.5,9 6.5,12.3 M6.5,.7 C9.5,4 9.5,9 6.5,12.3" fill="none" stroke="#fff" stroke-width=".8"/></svg>www.brantowork.co.uk</span>
  </footer>
</section>

</body>
</html>
```